Boutique Store Selling Antiques and Unique Finds

I need a Web Page designed for my Store Called "Willow Lane". I would like a very classic, muted design that looks European when pulled up. I will be selling Antiques from all over the world and Unique finds that have reproduced. I will also be selling high-end purses and jewelry with unique, reasonable products for the every-day buyer as well.

Target Market(s)

25-70 year old men and women;)

Coding

Coded - Design and coding required

Number of Pages Required

1 page

Colors

Designer to choose only greyscale colors for use in the design.

Requirements
Must have
• I want it

```html
<!DOCTYPE html>
<html lang="en">
<head>
<meta charset="utf-8">
<title>Willow Lane — Antiques &amp; Unique Finds</title>
<link href="https://fonts.googleapis.com/css2?family=Lato:wght@300;400;700&display=swap" rel="stylesheet">
<style>
  :root {
    --cream: #fdf9f1;
    --ink: #2b2a28;
    --muted: #6f6c68;
    --line: #8d8a86;
    --white: #ffffff;
    --footer: #5f5d5b;
    --label-bg: #fbf4e3;
  }
  * { margin: 0; padding: 0; box-sizing: border-box; }
  html, body { width: 1200px; height: 2996px; overflow: hidden; }
  body { background: var(--cream); font-family: 'Lato', sans-serif; color: var(--ink); position: relative; }
  .abs { position: absolute; }
  .center-x { left: 0; width: 1200px; text-align: center; }

  /* Header */
  .brand { top: 50px; font-size: 25px; letter-spacing: 6px; text-transform: uppercase; font-weight: 400; }
  .brand-dot { top: 16px; left: 585px; width: 30px; height: 30px; border: 2px solid var(--ink); border-radius: 50%; }
  .util { top: 6px; font-size: 13px; color: var(--muted); font-weight: 300; }
  .nav a { position: absolute; top: 97px; font-size: 14px; letter-spacing: 1px; color: var(--ink); text-decoration: none; }
  .nav a.active { color: var(--muted); }

  /* Hero */
  .hero { top: 128px; left: 0; width: 1200px; height: 515px; background: linear-gradient(90deg, #2c1f17 0%, #5a3a25 25%, #4a1c1c 45%, #2a2624 60%, #3d2a1e 78%, #1d1a1a 100%); }
  .hero-title { top: 290px; font-size: 60px; color: var(--white); letter-spacing: 3px; font-weight: 400; }
  .hero-sub { top: 360px; left: 370px; width: 460px; text-align: center; font-size: 19px; line-height: 29px; color: var(--white); }
  .btn { display: flex; align-items: center; justify-content: center; background: var(--white); border-radius: 26px; font-size: 16px; letter-spacing: 1px; color: var(--ink); box-shadow: 0 1px 6px rgba(0,0,0,.08); }
  .circle-btn { border-radius: 50%; display: flex; align-items: center; justify-content: center; }

  .section-title { font-size: 23px; letter-spacing: 1px; font-weight: 400; }
  .frame { border: 1px solid var(--line); }
  .divider { width: 1px; background: var(--line); }
  .col-label { font-size: 14px; letter-spacing: 2.5px; }

  .card { background: var(--white); border: 1px solid #d8d4ce; width: 234px; height: 338px; top: 875px; }
  .card .photo { position: absolute; left: 0; top: 0; width: 232px; height: 281px; }
  .card .tag { position: absolute; left: 7px; top: 7px; width: 218px; height: 44px; background: var(--label-bg); font-size: 13px; display: flex; align-items: center; justify-content: center; }
  .card .price { position: absolute; left: 0; top: 298px; width: 232px; text-align: center; font-size: 16px; }

  .about-photo { top: 1418px; left: 112px; width: 481px; height: 428px; background: linear-gradient(160deg, #5b3b24, #8a5530 50%, #3e2818); }
  .about-text { top: 1508px; left: 637px; width: 440px; font-size: 13.5px; line-height: 24px; color: #4a4845; font-weight: 300; }

  .have-photo { top: 2027px; width: 462px; height: 331px; }
  .have-name { top: 2377px; font-size: 13.5px; letter-spacing: .5px; text-align: center; }
  .have-price { top: 2402px; font-size: 13px; text-align: center; }

  .footer { top: 2599px; left: 0; width: 1200px; height: 328px; background: var(--footer); color: var(--white); }
  .footer h4 { position: absolute; top: 62px; font-size: 15.5px; font-weight: 400; letter-spacing: .3px; }
  .footer p { position: absolute; top: 102px; left: 110px; width: 230px; font-size: 13.5px; line-height: 22px; font-weight: 300; }
  .footer ul { position: absolute; top: 103px; list-style: none; font-size: 12px; letter-spacing: .4px; line-height: 24px; }
  .copyright { top: 2947px; font-size: 13px; letter-spacing: .3px; }
</style>
</head>
<body>

<!-- Header -->
<div class="abs brand-dot" aria-hidden="true"></div>
<div class="abs center-x brand">Willow Lane</div>
<div class="abs util" style="left:810px;">Sign in or Register</div>
<div class="abs util" style="left:957px; top:4px; display:flex; align-items:center; gap:4px;">
  <svg width="20" height="18" viewBox="0 0 20 18" fill="none" stroke="#6f6c68" stroke-width="1.4"><path d="M1 2h3l2.5 10h10l2-7H5.5"/><circle cx="8" cy="15.5" r="1.4"/><circle cx="15" cy="15.5" r="1.4"/></svg>
  <span>(0) Items</span>
</div>
<svg class="abs" style="left:1071px; top:7px;" width="16" height="16" viewBox="0 0 16 16" fill="none" stroke="#6f6c68" stroke-width="1.8"><circle cx="6.5" cy="6.5" r="4.5"/><path d="M10 10l4.5 4.5"/></svg>

<nav class="nav">
  <a class="active" style="left:159px;">HOME</a>
  <a style="left:237px;">SALE</a>
  <a style="left:304px;">NEW ARRIVALS</a>
  <a style="left:447px;">ANTIQUE &amp; UNIQUE</a>
  <a style="left:629px;">ACCESSORY</a>
  <a style="left:751px;">BOUTIQUE</a>
  <a style="left:865px;">GIFT</a>
  <a style="left:934px;">GIFT REGISTRY</a>
</nav>

<!-- Hero -->
<div class="abs hero" role="img" aria-label="Row of antique leather-bound books on a shelf"></div>
<div class="abs center-x hero-title">WILLOW LANE</div>
<div class="abs hero-sub">Sed ut perspiciatis unde omnis iste natus error sit voluptatem accusantium</div>
<div class="abs btn" style="left:490px; top:431px; width:220px; height:48px;">SHOP NOW</div>
<div class="abs circle-btn" style="left:28px; top:362px; width:62px; height:62px; border:1.5px solid #fff;">
  <svg width="22" height="18" viewBox="0 0 22 18" fill="none" stroke="#fff" stroke-width="2"><path d="M21 9H2M9 2L2 9l7 7"/></svg>
</div>
<div class="abs circle-btn" style="left:1109px; top:362px; width:62px; height:62px; border:1.5px solid #fff;">
  <svg width="22" height="18" viewBox="0 0 22 18" fill="none" stroke="#fff" stroke-width="2"><path d="M1 9h19M13 2l7 7-7 7"/></svg>
</div>
<div class="abs circle-btn" style="left:569px; top:617px; width:62px; height:62px; background:#fff; box-shadow:0 1px 6px rgba(0,0,0,.1);">
  <svg width="16" height="22" viewBox="0 0 16 22" fill="none" stroke="#555" stroke-width="1.8"><path d="M8 1v19M2 14l6 6 6-6"/></svg>
</div>

<!-- Our products -->
<div class="abs center-x section-title" style="top:740px;">OUR PRODUCTS</div>
<div class="abs frame" style="left:112px; top:813px; width:976px; height:415px;"></div>
<div class="abs divider" style="left:599px; top:813px; height:415px;"></div>
<div class="abs circle-btn" style="left:579px; top:792px; width:42px; height:42px; background:var(--cream); border:1px solid var(--line);">
  <svg width="12" height="18" viewBox="0 0 12 18" fill="none" stroke="#555" stroke-width="1.5"><path d="M6 1v15M1 11l5 5 5-5"/></svg>
</div>
<div class="abs col-label" style="left:112px; width:488px; top:833px; text-align:center;">ANTIQUE</div>
<div class="abs col-label" style="left:600px; width:488px; top:832px; text-align:center;">UNIQUE</div>

<div class="abs card" style="left:117px;">
  <div class="photo" role="img" aria-label="Ornate gilded crown resting on old books" style="background:linear-gradient(180deg,#d9d3cb,#9b7b48 60%,#4a3424);"></div>
  <div class="tag">LARGE CROWN</div>
  <div class="price">$450.00</div>
</div>
<div class="abs card" style="left:359px;">
  <div class="photo" role="img" aria-label="French jewelled crown on a dark pedestal" style="background:linear-gradient(180deg,#3a2f26,#b08a5c 55%,#2d2b2a);"></div>
  <div class="tag">LARGER FRENCH CROWN</div>
  <div class="price">$450.00</div>
</div>
<div class="abs card" style="left:606px;">
  <div class="photo" role="img" aria-label="Enamel medal hanging from a ribbon" style="background:linear-gradient(180deg,#cfc7bc,#a99a86 60%,#c7beb2);"></div>
  <div class="tag">CLOISONNE ENAMEL VASE</div>
  <div class="price">$450.00</div>
</div>
<div class="abs card" style="left:849px;">
  <div class="photo" role="img" aria-label="Antique iron helmet on a stack of design books" style="background:linear-gradient(180deg,#b9b2a6,#55524e 55%,#7a5a3e);"></div>
  <div class="tag">LUXURIOUS GOLDEN SOFA</div>
  <div class="price">$450.00</div>
</div>

<div class="abs btn" style="left:490px; top:1269px; width:221px; height:50px;">VIEW ALL</div>

<!-- About -->
<div class="abs about-photo" role="img" aria-label="Wood-panelled stairway with chandelier and carved statue"></div>
<div class="abs section-title" style="left:637px; top:1458px;">ABOUT US</div>
<p class="abs about-text">Sed ut perspiciatis unde omnis iste natus error sit voluptatem accusantium doloremque laudantium, totam rem aperiam, eaque ipsa quae ab illo inventore veritatis et quasi architecto beatae vitae dicta sunt explicabo. Nemo enim ipsam voluptatem quia voluptas sit aspernatur aut odit aut fugit, sed quia consequuntur magni dolores eos qui ratione voluptatem sequi nesciunt. Neque porro quisquam est, qui dolorem ipsum quia dolor sit amet, consectetur, adipisci velit, sed quia non numquam eius modi tempora incidunt ut labore et dolore magnam aliquam quaerat voluptatem.</p>
<div class="abs btn" style="left:637px; top:1753px; width:221px; height:50px;">READ MORE</div>

<!-- What we have -->
<div class="abs center-x section-title" style="top:1926px;">WHAT WE HAVE</div>
<div class="abs frame" style="left:112px; top:2012px; width:976px; height:428px;"></div>
<div class="abs divider" style="left:599px; top:2012px; height:428px;"></div>
<div class="abs circle-btn" style="left:579px; top:1984px; width:42px; height:42px; background:var(--cream); border:1px solid var(--line);">
  <svg width="12" height="18" viewBox="0 0 12 18" fill="none" stroke="#555" stroke-width="1.5"><path d="M6 1v15M1 11l5 5 5-5"/></svg>
</div>
<div class="abs have-photo" role="img" aria-label="Row of antique leather-bound books" style="left:122px; background:linear-gradient(90deg,#2c1f17,#7a5232 25%,#5a1f1f 45%,#2b2725 65%,#3e2b1f 85%,#1f1b1a);"></div>
<div class="abs have-photo" role="img" aria-label="Box of leather swatches, ribbons and trims" style="left:616px; background:linear-gradient(120deg,#b4a27a,#e7e0d0 35%,#3a3a3c 60%,#7a6a55 80%,#2a2a30);"></div>
<div class="abs have-name" style="left:122px; width:462px;">TURQUOISE GRAMOPHONE</div>
<div class="abs have-price" style="left:122px; width:462px;">$450.00</div>
<div class="abs have-name" style="left:616px; width:462px;">ENIM ADMINIMA VENIAM</div>
<div class="abs have-price" style="left:616px; width:462px;">$450.00</div>

<div class="abs btn" style="left:490px; top:2479px; width:221px; height:50px;">VIEW ALL</div>

<!-- Footer -->
<footer class="abs footer">
  <h4 style="left:112px;">ABOUT US</h4>
  <p>Sed ut perspiciatis unde omnis iste natus error sit voluptatem accusantium doloremque laudantium, totam rem aperiam, eaque ipsa quae ab illo inventore veritatis et quasi</p>
  <h4 style="left:452px;">QUICK LINKS</h4>
  <ul style="left:452px;">
    <li>HOME</li><li>SALE</li><li>NEW ARRIVALS</li><li>ANTIQUE &amp; UNIQUE</li><li>ACCESSORY</li><li>BOUTIQUE</li><li>GIFT</li><li>GIFT REGISTRY</li>
  </ul>
  <h4 style="left:679px;">TERMS AND CONDITIONS</h4>
  <ul style="left:679px;">
    <li>TERMS AND CONDITIONS</li><li>PRIVACY POLICY</li><li>GDPR</li>
  </ul>
  <h4 style="left:972px;">SOCIAL</h4>
  <ul style="left:972px;">
    <li>PICTOGRAPH</li><li>FRIENDBOOK</li><li>PINSHELF</li><li>CHIRPER</li>
  </ul>
</footer>
<div class="abs center-x copyright">COPYRIGHT © 2021.&nbsp; ALL RIGHTS RESERVED</div>

</body>
</html>
```